DESIGN OF STATIONERY - TORVALE MED

WE WORK IN THE FIELD OF HEALTH (IMAGING: MRI - CT ETC.).
WE WOULD LIKE TO CREATE THE ENTIRE STATIONERY DESIGN : LETTERHEAD, BUSINESS CARD, CALENDAR, INVOICES, CD HOLDER, ETC.

Target Market(s)

PERSONS UNDERTAKING HEALTH EXAMINATIONS

```html
<!DOCTYPE html>
<html lang="en">
<head>
<meta charset="utf-8">
<title>Torvale Med Stationery</title>
<link href="https://fonts.googleapis.com/css2?family=Montserrat:wght@400;500;600;700&family=Open+Sans:wght@400&display=swap" rel="stylesheet">
<style>
:root{
  --bg:#dedede;
  --paper:#ffffff;
  --brand-blue:#0e72bb;
  --brand-teal:#17a59a;
  --ink:#1d2b44;
  --text:#4a4a4a;
  --rule:#3a3a3a;
  --row-a:#f1f1f3;
  --row-b:#e8e8ea;
  --tint-mint:#eef6f4;
  --tint-blue:#edf2f9;
}
*{margin:0;padding:0;box-sizing:border-box}
html,body{width:1200px;height:800px;overflow:hidden;background:var(--bg)}
body{position:relative;font-family:'Montserrat',sans-serif;color:var(--ink)}
.sheet{position:absolute;background:var(--paper);box-shadow:0 4px 14px rgba(0,0,0,.12)}
.invoice{left:164px;top:111px;width:412px;height:574px}
.letter{left:612px;top:110px;width:408px;height:574px;font-family:'Open Sans',sans-serif}
.abs{position:absolute}
.brand{position:absolute;top:38px;left:27px}
.brand-name{font-family:'Montserrat',sans-serif;font-weight:700;font-size:20px;color:var(--brand-blue);letter-spacing:-.2px;display:flex;align-items:center;gap:5px;line-height:1}
.brand-name .mark{width:8px;height:8px;background:var(--brand-teal)}
.brand-tag{font-family:'Montserrat',sans-serif;font-size:5.6px;font-weight:500;color:var(--brand-teal);margin-top:4px}
.contact{font-size:6.6px;color:var(--text);line-height:8.6px}
.contact svg{width:6px;height:6px;vertical-align:-1px;margin-right:2px;fill:var(--brand-blue)}
.invoice-title{left:27px;top:114px;font-size:12px;font-weight:600}
.date-label{left:302px;top:118px;font-size:7.5px;font-weight:600}
.field{position:absolute;font-size:7.5px;font-weight:500;display:flex;align-items:flex-end}
.field .line{border-bottom:1px solid var(--rule);margin-left:5px;height:1px}
.items{position:absolute;left:27px;top:190px;width:358px;border-collapse:collapse;font-size:9px}
.items th{background:var(--brand-blue);color:#fff;font-weight:500;height:23px;border-left:1px solid var(--rule);border-right:1px solid var(--rule)}
.items td{height:20.8px;border-left:1px solid var(--rule);border-right:1px solid var(--rule)}
.items tbody tr:nth-child(odd) td{background:var(--row-a)}
.items tbody tr:nth-child(even) td{background:var(--row-b)}
.items tbody tr:last-child td{border-bottom:1px solid var(--rule)}
.totals{position:absolute;left:260px;top:443px;width:125px;border-collapse:collapse;font-size:7.5px;font-weight:500}
.totals td{height:21px;border:1px solid var(--rule);padding-left:9px}
.totals td:first-child{width:63px}
.pay{left:27px;top:456px;display:flex;gap:13px;font-size:7.5px;color:var(--text)}
.pay span{display:flex;align-items:center;gap:3px}
.pay i{width:8px;height:8px;border:1px solid var(--rule)}
.sign-note{left:27px;top:485px;font-size:7.5px;color:var(--text);line-height:11px}
.letter .brand{left:41px;top:40px}
.letter-body{left:41px;top:140px;width:328px;font-size:7.5px;line-height:10.8px;color:var(--text)}
.letter-body p{text-align:justify;margin-bottom:10.8px}
.letter-body p.plain{text-align:left}
.signature{left:41px;top:425px;width:47px;height:45px;background:linear-gradient(135deg,#e9ecf2,#dfe4ee);border-radius:3px}
.tile{position:absolute}
</style>
</head>
<body>

<section class="sheet invoice">
  <div class="brand">
    <div class="brand-name"><span class="mark"></span>Torvale Med</div>
    <div class="brand-tag">Health Care Diagnostic</div>
  </div>
  <div class="abs contact" style="left:304px;top:28px">
    Marlow Court, 18 Fenwick<br>Road, London SE4 7PL
    <div style="margin-top:3px">
      <div><svg viewBox="0 0 10 10"><path d="M2 1l2 2-1 1.5c.7 1.4 1.6 2.3 3 3L7.5 6l2 2-1.5 1.5C4.5 9 1 5.5.5 2.5z"/></svg>0200 555 0148</div>
      <div><svg viewBox="0 0 10 10"><path d="M0 2h10v6H0zM1 3v.3L5 6l4-2.7V3L5 5.5z"/></svg>info@torvalemed.com</div>
      <div><svg viewBox="0 0 10 10"><circle cx="5" cy="5" r="4.5" fill="none" stroke="#0e72bb" stroke-width="1"/><path d="M.5 5h9M5 .5v9" stroke="#0e72bb" stroke-width=".8"/></svg>www.torvalemed.com</div>
    </div>
  </div>

  <div class="abs invoice-title">INVOICE # :</div>
  <div class="abs date-label">DATE :</div>
  <div class="field" style="left:27px;top:133px">Customer :<span class="line" style="width:313px"></span></div>
  <div class="field" style="left:27px;top:150px">Address :<span class="line" style="width:318px"></span></div>
  <div class="field" style="left:27px;top:166px">Phone :<span class="line" style="width:155px"></span><span style="margin-left:4px">Fax :</span><span class="line" style="width:143px"></span></div>

  <table class="items">
    <thead><tr><th style="width:47px">QTY</th><th style="width:187px">DESCRIPTION</th><th style="width:62px">PRICE</th><th>AMOUNT</th></tr></thead>
    <tbody>
      <tr><td></td><td></td><td></td><td></td></tr>
      <tr><td></td><td></td><td></td><td></td></tr>
      <tr><td></td><td></td><td></td><td></td></tr>
      <tr><td></td><td></td><td></td><td></td></tr>
      <tr><td></td><td></td><td></td><td></td></tr>
      <tr><td></td><td></td><td></td><td></td></tr>
      <tr><td></td><td></td><td></td><td></td></tr>
      <tr><td></td><td></td><td></td><td></td></tr>
      <tr><td></td><td></td><td></td><td></td></tr>
      <tr><td></td><td></td><td></td><td></td></tr>
      <tr><td></td><td></td><td></td><td></td></tr>
    </tbody>
  </table>

  <table class="totals">
    <tr><td>SUB TOTAL</td><td></td></tr>
    <tr><td>GST #</td><td></td></tr>
    <tr><td>SUBTOTAL</td><td></td></tr>
  </table>

  <div class="abs pay">
    <span><i></i>VISA</span><span><i></i>MC</span><span><i></i>DEBIT</span><span><i></i>CASH</span><span><i></i>CHEQUE</span>
  </div>
  <div class="abs sign-note">Signature Indicates<br>Acceptance of Price and term</div>
</section>

<section class="sheet letter">
  <div class="brand">
    <div class="brand-name"><span class="mark"></span>Torvale Med</div>
    <div class="brand-tag">Health Care Diagnostic</div>
  </div>
  <div class="abs contact" style="left:194px;top:36px;font-family:'Montserrat',sans-serif">
    <div><svg viewBox="0 0 10 10"><path d="M2 1l2 2-1 1.5c.7 1.4 1.6 2.3 3 3L7.5 6l2 2-1.5 1.5C4.5 9 1 5.5.5 2.5z"/></svg>07700 900 462</div>
    <div><svg viewBox="0 0 10 10"><path d="M0 2h10v6H0zM1 3v.3L5 6l4-2.7V3L5 5.5z"/></svg>info@torvalemed.com</div>
    <div><svg viewBox="0 0 10 10"><circle cx="5" cy="5" r="5"/></svg>www.torvalemed.com</div>
  </div>
  <div class="abs contact" style="left:286px;top:36px;font-family:'Montserrat',sans-serif">
    Torvale-Med-R<br>2nd Floor 9 Ashgrove<br>Place Leeds LS2 8QT
  </div>

  <div class="abs letter-body">
    <p class="plain">Dear customer,</p>
    <p>Lorem ipsum dolor sit amet, consectetur adipisicing elit, sed do eiusmod tempor incididunt ut labore et dolore magna aliqua. Ut enim ad minim veniam, quis nostrud exercitation ullamco laboris nisi ut aliquip ex ea commodo consequat. Duis aute irure dolor in reprehenderit in voluptate velit esse cillum dolore eu fugiat nulla pariatur. Excepteur sint occaecat cupidatat non proident, sunt in culpa qui officia deserunt mollit anim id est laborum.</p>
    <p>Lorem ipsum dolor sit amet, consectetur adipisicing elit, sed do eiusmod tempor incididunt ut labore et dolore magna aliqua. Ut enim ad minim veniam, quis nostrud exercitation ullamco laboris nisi ut aliquip ex ea commodo consequat. Duis aute irure dolor in reprehenderit in voluptate velit esse cillum dolore eu fugiat nulla pariatur. Excepteur sint occaecat cupidatat non proident, sunt in culpa qui officia deserunt mollit anim id est laborum.</p>
    <p>Lorem ipsum dolor sit amet, consectetur adipisicing elit, sed do eiusmod tempor incididunt ut labore et dolore magna aliqua. Ut enim ad minim veniam, quis nostrud exercitation ullamco laboris nisi ut aliquip ex ea commodo consequat. Duis aute irure dolor in reprehenderit in voluptate velit esse cillum dolore eu fugiat nulla pariatur. Excepteur sint occaecat cupidatat non proident, sunt in culpa qui officia deserunt mollit anim id est laborum.</p>
    <p>Lorem ipsum dolor sit amet, consectetur adipisicing elit, sed do eiusmod tempor incididunt ut labore et dolore magna aliqua. Ut enim ad minim veniam, quis nostrud exercitation ullamco laboris nisi ut aliquip ex ea commodo consequat. Duis aute irure dolor in reprehenderit.</p>
    <p class="plain">Yours Sincerely,</p>
  </div>
  <div class="abs signature" role="img" aria-label="Handwritten signature of the sender"></div>

  <div class="tile" style="left:319px;top:441px;width:43px;height:40px;background:var(--tint-mint)"></div>
  <div class="tile" style="left:362px;top:481px;width:41px;height:43px;background:var(--tint-mint)"></div>
  <div class="tile" style="left:274px;top:486px;width:83px;height:42px;background:var(--tint-blue)"></div>
  <div class="tile" style="left:314px;top:528px;width:43px;height:40px;background:var(--tint-blue)"></div>
</section>

</body>
</html>
```